Pizza Coupon App Design Project

*******This project will have a guaranteed payout once I see that there is quality work being designed*********

I require the design (no coding) of 4 vertical screens (the screen will not change for horizontal orientation) for Zentrix and Orbalis. The highest res should be used so it can be scaled for older generation phones.

The mobile app will be used to access pizza coupons.

I do not have a specific style or look that I am going for, although I do not want a childish design (e.g. comic sans). The main requirements are for it to be very easy for users to understand and navigate and to be clean and professional.

I am happy if you only produce a design of the main and store selection screens to which I will give feedback before continuing to design the remaining screens.

The selected artist must be flexible in adapting the final design slightly after the contest is completed, during the app development process (maybe a few small modifications over a month or so).
Please do not include any copyrighted images in your deliverables. I must be the sole owner of the graphics once I have paid for them.

I have included attachments which show the process flow and the screen requirements so that will give you the detail you need to design them. I have also included the logo to assist you in your design., *******This project is now guaranteed *********

I have included attachments which show the process flow and the screen requirements so that will give you the detail you need to design them. I have also included the logo to assist you in your design., *******This project will have a guaranteed payout once I see that there is quality work being designed*********

I have included attachments which show the process flow and the screen requirements so that will give you the detail you need to design them. I have also included the logo to assist you in your design.

Reason: Still looking for the perfect design! ******Project is now guaranteed******

******Project is now guaranteed******

Reason: Starting to get some great designs, we are getting much closer! Keep it up.

Target Market(s)

students and 18-30 year olds - People who want cheap meals and people who order pizza online., students and 18-30 year olds - People who want cheap meals and people who order pizza online., students and 18-30 year olds - People who want cheap meals and people who order pizza online.

Industry/Entity Type

Store

Requirements
Must have
• Must have requirements are listed in the attached documents., Must have requirements are listed in the attached documents., Must have requirements are listed in the attached documents.

```html
<!DOCTYPE html>
<html lang="en">
<head>
<meta charset="utf-8">
<title>Pizza Coupons – Store Coupons Screen</title>
<link rel="stylesheet" href="https://fonts.googleapis.com/css2?family=PT+Sans:wght@400;700&family=Open+Sans:wght@400;600;700&display=swap">
<style>
  :root {
    --stage: #e9e9e9;
    --screen-bg: #f1ede8;
    --ad-top: #6a6a6a;
    --ad-bottom: #4a4a4a;
    --ad-text: #8d8d8d;
    --ink: #2b2b2b;
    --coupon-top: #f8ad5c;
    --coupon-bottom: #f08a2c;
    --coupon-edge: #e07a22;
    --coupon-text: #d9521d;
    --coupon-text-dark: #2e1d12;
    --stub-red-top: #d9593a;
    --stub-red-bottom: #b63b22;
    --stub-brown-top: #6b3a22;
    --stub-brown-bottom: #4a2412;
    --ticket-fill: #f1a052;
    --price-dark: #3a1208;
    --track: #3c3c3c;
    --thumb: #c0504a;
    --pill-top: #fbfbfb;
    --pill-bottom: #cfcfcf;
  }
  * { box-sizing: border-box; margin: 0; padding: 0; }
  html, body { width: 1200px; height: 949px; overflow: hidden; background: var(--stage); }
  body { font-family: "PT Sans", sans-serif; color: var(--ink); }

  .screen {
    position: absolute; left: 290px; top: 14px; width: 620px; height: 920px;
    background: var(--screen-bg); overflow: hidden;
    box-shadow: 0 0 0 1px #d4d0cb;
  }
  .ad-banner {
    height: 130px; background: linear-gradient(var(--ad-top), var(--ad-bottom));
    display: flex; align-items: center; justify-content: center;
    font-family: "Open Sans", sans-serif; font-size: 36px; color: var(--ad-text);
    text-shadow: 0 1px 0 #777;
  }

  .order-type {
    position: absolute; left: 320px; top: 144px; width: 250px; height: 44px;
    border-radius: 14px; border: 1px solid #9a9a9a;
    background: linear-gradient(var(--pill-top), var(--pill-bottom));
    display: flex; align-items: center; overflow: hidden;
  }
  .order-type svg { margin-left: 14px; }
  .order-type .label { flex: 1; font-family: "Open Sans", sans-serif; font-size: 25px; margin-left: 16px; }
  .order-type .toggle {
    width: 56px; height: 100%; border-left: 1px solid #9a9a9a;
    background: linear-gradient(#e2e2e2, #a9a9a9);
    display: flex; align-items: center; justify-content: center;
  }

  .store-title {
    position: absolute; left: 24px; top: 202px; display: flex; align-items: center; gap: 16px;
    font-family: "Open Sans", sans-serif; font-size: 30px; color: #222;
  }

  .coupon-list { position: absolute; left: 20px; top: 258px; width: 540px; }
  .coupon {
    height: 104px; margin-bottom: 12px; display: flex; border-radius: 8px; overflow: hidden;
    background: linear-gradient(var(--coupon-top), var(--coupon-bottom));
    box-shadow: 0 2px 3px rgba(0,0,0,.25), inset 0 0 0 2px var(--coupon-edge);
  }
  .coupon .offer { flex: 1; padding: 14px 18px 0 22px; }
  .coupon .offer-text {
    font-weight: 700; font-size: 19px; line-height: 22px; text-transform: uppercase;
    color: var(--coupon-text); text-shadow: 0 1px 0 rgba(255,255,255,.35);
  }
  .coupon.is-plain .offer-text { color: var(--coupon-text-dark); }
  .coupon .shared { font-family: "Open Sans", sans-serif; font-size: 11px; color: #5a3516; margin-top: 6px; }
  .coupon .shared b { font-size: 12px; margin-left: 10px; color: #3a2212; }

  .stub {
    width: 160px; position: relative; padding: 8px 10px 0 12px;
    border-left: 3px dotted var(--screen-bg);
    background: linear-gradient(var(--stub-red-top), var(--stub-red-bottom));
  }
  .stub.is-brown { background: linear-gradient(var(--stub-brown-top), var(--stub-brown-bottom)); }
  .stub .copy-label { font-family: "Open Sans", sans-serif; font-size: 11px; color: #3a1a10; text-align: right; padding-right: 18px; }
  .stub.is-brown .copy-label { color: #e0b090; }
  .code-ticket {
    margin: 2px 0 0 22px; height: 40px; border: 3px dashed #2a150c; border-radius: 8px;
    background: var(--ticket-fill); display: flex; align-items: center; justify-content: center;
    font-family: "Open Sans", sans-serif; font-size: 19px; color: #3a2010; letter-spacing: 1px;
  }
  .stub svg { position: absolute; left: 6px; top: 26px; }
  .price { text-align: right; padding-right: 8px; margin-top: 3px; font-weight: 700; font-size: 22px; color: var(--price-dark); }
  .price small { font-size: 14px; }

  .scroll-track {
    position: absolute; left: 582px; top: 150px; width: 14px; height: 560px;
    border-radius: 7px; background: var(--track);
  }
  .scroll-thumb { width: 100%; height: 130px; border-radius: 7px; background: linear-gradient(90deg, #a63a36, var(--thumb), #a63a36); }

  .settings { position: absolute; left: 570px; top: 722px; }
  .back { position: absolute; left: 24px; top: 860px; }
</style>
</head>
<body>
<main class="screen">
  <header class="ad-banner">Advertising</header>

  <div class="order-type">
    <svg width="34" height="28" viewBox="0 0 34 28" aria-hidden="true">
      <path d="M9 10 L17 3 L25 10" fill="none" stroke="#333" stroke-width="2"/>
      <path d="M3 10 H31 L28 25 H6 Z" fill="none" stroke="#333" stroke-width="2"/>
    </svg>
    <span class="label">Pickup</span>
    <span class="toggle">
      <svg width="22" height="14" viewBox="0 0 22 14" aria-hidden="true"><path d="M1 1 H21 L11 13 Z" fill="#555"/></svg>
    </span>
  </div>

  <h1 class="store-title">
    <svg width="44" height="40" viewBox="0 0 44 40" aria-hidden="true">
      <path d="M2 4 H42 L40 14 H4 Z" fill="#4a4a4a"/>
      <rect x="5" y="16" width="34" height="22" fill="#4a4a4a"/>
      <rect x="11" y="22" width="22" height="16" fill="#f1ede8"/>
    </svg>
    STORE 1
  </h1>

  <section class="coupon-list">
    <article class="coupon">
      <div class="offer">
        <p class="offer-text">What you get for using the coupon. What you'll get for using the coupoun.</p>
        <p class="shared">Shared by:<b>example-user</b></p>
      </div>
      <div class="stub">
        <p class="copy-label">Copy code:</p>
        <svg width="30" height="24" viewBox="0 0 30 24" aria-hidden="true"><circle cx="6" cy="6" r="4" fill="none" stroke="#1b0c06" stroke-width="2.5"/><circle cx="6" cy="18" r="4" fill="none" stroke="#1b0c06" stroke-width="2.5"/><path d="M9 8 L29 19 M9 16 L29 5" stroke="#1b0c06" stroke-width="2.5"/></svg>
        <div class="code-ticket">XXXXXX</div>
        <p class="price"><small>AU$</small> 5.00</p>
      </div>
    </article>

    <article class="coupon">
      <div class="offer">
        <p class="offer-text">What you get for using the coupon. What you'll get for using the coupoun.</p>
        <p class="shared">Shared by:<b>example-user</b></p>
      </div>
      <div class="stub is-brown">
        <p class="copy-label">Copy code:</p>
        <svg width="30" height="24" viewBox="0 0 30 24" aria-hidden="true"><circle cx="6" cy="6" r="4" fill="none" stroke="#1b0c06" stroke-width="2.5"/><circle cx="6" cy="18" r="4" fill="none" stroke="#1b0c06" stroke-width="2.5"/><path d="M9 8 L29 19 M9 16 L29 5" stroke="#1b0c06" stroke-width="2.5"/></svg>
        <div class="code-ticket">XXXXXX</div>
        <p class="price"><small>AU$</small> 15.00</p>
      </div>
    </article>

    <article class="coupon">
      <div class="offer">
        <p class="offer-text">What you get for using the coupon. What you'll get for using the coupoun.</p>
        <p class="shared">Shared by:<b>example-user</b></p>
      </div>
      <div class="stub">
        <p class="copy-label">Copy code:</p>
        <svg width="30" height="24" viewBox="0 0 30 24" aria-hidden="true"><circle cx="6" cy="6" r="4" fill="none" stroke="#1b0c06" stroke-width="2.5"/><circle cx="6" cy="18" r="4" fill="none" stroke="#1b0c06" stroke-width="2.5"/><path d="M9 8 L29 19 M9 16 L29 5" stroke="#1b0c06" stroke-width="2.5"/></svg>
        <div class="code-ticket">Copied</div>
        <p class="price"><small>AU$</small> 15.00</p>
      </div>
    </article>

    <article class="coupon">
      <div class="offer">
        <p class="offer-text">What you get for using the coupon. What you'll get for using the coupoun.</p>
        <p class="shared">Shared by:<b>example-user</b></p>
      </div>
      <div class="stub">
        <p class="copy-label">Copy code:</p>
        <svg width="30" height="24" viewBox="0 0 30 24" aria-hidden="true"><circle cx="6" cy="6" r="4" fill="none" stroke="#1b0c06" stroke-width="2.5"/><circle cx="6" cy="18" r="4" fill="none" stroke="#1b0c06" stroke-width="2.5"/><path d="M9 8 L29 19 M9 16 L29 5" stroke="#1b0c06" stroke-width="2.5"/></svg>
        <div class="code-ticket">XXXXXX</div>
        <p class="price"><small>AU$</small> 10.00</p>
      </div>
    </article>

    <article class="coupon is-plain">
      <div class="offer">
        <p class="offer-text">What you get for using the coupon. What you'll get for using the coupoun.</p>
        <p class="shared">Shared by:<b>example-user</b></p>
      </div>
    </article>
  </section>

  <div class="scroll-track"><div class="scroll-thumb"></div></div>

  <svg class="settings" width="40" height="40" viewBox="0 0 40 40" aria-label="Settings" role="img">
    <g fill="#333" transform="translate(20 20)">
      <rect x="-4" y="-18" width="8" height="36" rx="1"/>
      <rect x="-4" y="-18" width="8" height="36" rx="1" transform="rotate(45)"/>
      <rect x="-4" y="-18" width="8" height="36" rx="1" transform="rotate(90)"/>
      <rect x="-4" y="-18" width="8" height="36" rx="1" transform="rotate(135)"/>
      <circle r="13"/>
    </g>
    <circle cx="20" cy="20" r="5.5" fill="#f1ede8"/>
  </svg>

  <svg class="back" width="60" height="32" viewBox="0 0 60 32" aria-label="Back" role="img">
    <path d="M58 16 H10 M20 5 L6 16 L20 27" fill="none" stroke="#333" stroke-width="5"/>
  </svg>
</main>
</body>
</html>
```